Xmas card for doggie day care

I’d like a Xmas card designed specifically for our doggie day care.
We have some ideas and examples to inspire creators (see photos). The idea is to look more artistic rather than computer generated. Our dogs are in majority small and medium sized, so it would be good to reflect that with a couple of larger breeds like labradors and labradoodle.
Picture one on the attachment: we like the frame on it and it would be great to use the same. Adding our logo inside the baubles on the sides. (Logo attached)
Size: 148x148 mm cards
Format: pdf or other good format to send to the printer company

Company colours: turquoise and rose golden or orange

Requirements
Must have
• Artistic, hand drawn style, instead of computer generated
Nice to have
• The frame used on the first photo attached. Adding our logo inside the baubles on the sides. (Logo attached)
Should not have
• Computer generated style

```html
<!DOCTYPE html>
<html lang="en">
<head>
<meta charset="utf-8">
<title>Pawprint Play Society – Christmas Card</title>
<link href="https://fonts.googleapis.com/css2?family=Lilita+One&family=Playfair+Display:wght@700&family=Bebas+Neue&display=swap" rel="stylesheet">
<style>
  :root {
    --workspace: #888888;
    --card-red: #a3141f;
    --card-red-deep: #7d0d16;
    --gold-light: #f6dd7a;
    --gold: #d9a72c;
    --gold-dark: #a87718;
    --ribbon-green: #0d6a24;
    --ribbon-green-dark: #06461a;
    --title-green: #0b5a1f;
    --cream: #efe8da;
    --floor: #8a5a35;
    --white: #ffffff;
  }
  html, body {
    margin: 0;
    width: 1184px;
    height: 1200px;
    overflow: hidden;
    background: var(--workspace);
  }
  .card { display: block; width: 1184px; height: 1200px; }
  .club-name {
    font-family: "Lilita One", sans-serif;
    font-size: 47px;
    letter-spacing: 2px;
    fill: var(--title-green);
  }
  .crest-name {
    font-family: "Lilita One", sans-serif;
    font-size: 26px;
    fill: var(--card-red-deep);
  }
  .greeting-merry {
    font-family: "Playfair Display", serif;
    font-weight: 700;
    font-size: 74px;
    fill: var(--white);
  }
  .greeting-christmas {
    font-family: "Bebas Neue", sans-serif;
    font-size: 196px;
    stroke: var(--card-red-deep);
    stroke-width: 18px;
    stroke-linejoin: round;
    paint-order: stroke;
  }
</style>
</head>
<body>
<svg class="card" viewBox="0 0 1184 1200" xmlns="http://www.w3.org/2000/svg">
  <defs>
    <linearGradient id="goldGrad" x1="0" y1="0" x2="1" y2="1">
      <stop offset="0" stop-color="var(--gold-dark)"/>
      <stop offset="0.35" stop-color="var(--gold-light)"/>
      <stop offset="0.65" stop-color="var(--gold)"/>
      <stop offset="1" stop-color="var(--gold-light)"/>
    </linearGradient>
    <linearGradient id="titleGold" x1="0" y1="0" x2="0" y2="1">
      <stop offset="0" stop-color="#fff1a8"/>
      <stop offset="0.5" stop-color="#d9a72c"/>
      <stop offset="1" stop-color="#f3d372"/>
    </linearGradient>
    <radialGradient id="redGrad" cx="0.5" cy="0.45" r="0.75">
      <stop offset="0" stop-color="#b81c27"/>
      <stop offset="1" stop-color="var(--card-red-deep)"/>
    </radialGradient>
    <linearGradient id="sceneGrad" x1="0" y1="0" x2="0" y2="1">
      <stop offset="0" stop-color="var(--cream)"/>
      <stop offset="0.45" stop-color="#9fc1cf"/>
      <stop offset="0.62" stop-color="#5f9a4c"/>
      <stop offset="0.78" stop-color="var(--floor)"/>
      <stop offset="1" stop-color="#6c4427"/>
    </linearGradient>
    <radialGradient id="baubleGrad" cx="0.4" cy="0.35" r="0.7">
      <stop offset="0" stop-color="#f7c94a"/>
      <stop offset="1" stop-color="#d28a12"/>
    </radialGradient>
    <clipPath id="sceneClip"><circle cx="592" cy="582" r="362"/></clipPath>
    <path id="clubArc" d="M331 296 A388 388 0 0 1 853 296"/>
    <path id="merryArc" d="M440 900 Q615 850 790 900"/>
  </defs>

  <!-- card frame -->
  <rect class="card-border" x="107" y="107" width="970" height="973" fill="url(#goldGrad)"/>
  <rect class="card-field" x="117" y="117" width="950" height="953" fill="url(#redGrad)"
        role="img" aria-label="Ornate red swirl and snowflake pattern"/>

  <!-- hanging baubles -->
  <g class="bauble bauble-left">
    <line x1="181" y1="117" x2="181" y2="270" stroke="var(--gold)" stroke-width="4" stroke-dasharray="3 3"/>
    <rect x="168" y="270" width="26" height="22" rx="3" fill="var(--gold-dark)"/>
    <circle cx="181" cy="363" r="71" fill="url(#baubleGrad)" role="img" aria-label="Gold Christmas bauble with red and green zigzag bands"/>
  </g>
  <g class="bauble bauble-right">
    <line x1="996" y1="117" x2="996" y2="270" stroke="var(--gold)" stroke-width="4" stroke-dasharray="3 3"/>
    <rect x="983" y="270" width="26" height="22" rx="3" fill="var(--gold-dark)"/>
    <circle cx="996" cy="363" r="71" fill="url(#baubleGrad)" role="img" aria-label="Gold Christmas bauble with red and green zigzag bands"/>
  </g>

  <!-- central medallion -->
  <circle class="medallion-ring" cx="592" cy="582" r="408" fill="url(#goldGrad)"/>
  <circle cx="592" cy="582" r="398" fill="var(--card-red)"/>
  <circle cx="592" cy="582" r="378" fill="url(#goldGrad)"/>
  <circle cx="592" cy="582" r="368" fill="var(--gold-light)"/>
  <g clip-path="url(#sceneClip)">
    <rect x="230" y="220" width="724" height="724" fill="url(#sceneGrad)"
          role="img" aria-label="Festive room with striped wallpaper, bunting, two snowy windows, a decorated Christmas tree with presents, and four small dogs in elf hats on a wooden floor"/>
  </g>

  <!-- club mark in crest position -->
  <g class="crest-mark">
    <circle cx="510" cy="330" r="12" fill="var(--card-red-deep)"/>
    <text class="crest-name" x="530" y="339">Pawprint Play</text>
  </g>

  <!-- top gold ribbon with club name -->
  <path class="club-ribbon"
        d="M280 268 A434 434 0 0 1 904 268 L846 334 A352 352 0 0 0 338 334 Z"
        fill="url(#goldGrad)"/>
  <text class="club-name"><textPath href="#clubArc" startOffset="50%" text-anchor="middle">PAWPRINT PLAY SOCIETY</textPath></text>

  <!-- green greeting ribbon -->
  <polygon class="ribbon-tail" points="347,792 448,768 452,880 430,884 360,856 378,820" fill="var(--ribbon-green-dark)"/>
  <polygon class="ribbon-tail" points="860,792 760,768 756,880 778,884 850,856 830,820" fill="var(--ribbon-green-dark)"/>
  <path class="ribbon-band" d="M425 845 Q615 790 805 845 L800 930 Q615 880 430 930 Z" fill="var(--ribbon-green)"/>
  <text class="greeting-merry"><textPath href="#merryArc" startOffset="50%" text-anchor="middle">MERRY</textPath></text>

  <!-- Christmas title -->
  <text class="greeting-christmas" x="596" y="1030" text-anchor="middle" textLength="560" lengthAdjust="spacingAndGlyphs" fill="url(#titleGold)">CHRISTMAS</text>
</svg>
</body>
</html>
```